Yard sign design for high end luxury home builder.

Need a design for signage on custom homes that are being built. I already have a logo that I am satisfied with that needs to be incorporated. I need the following incorporated in the design of the sign-
- Lic number 381526
- phone number (805) 555-0148‬
- quennbuilderscrew.com
- Logo/Branding

If possible it may be nice to have the following quote that is on are business cards-

Quote from Gerard of Norvelle-
HE WHO WORKS WITH HIS HANDS IS A LABORER.
HE WHO WORKS WITH HIS HANDS & HIS HEAD IS A CRAFTSMAN.
HE WHO WORKS WITH HIS HANDS & HIS HEAD & HIS HEART IS AN ARTISAN.
-GERARD OF NORVELLE

Target Market(s)

Archetect, Designers, Clients desiring to build a new home or remodel.

Colors
fde9d4
fee4d5
fabb94
fac994
faa54b
f68d4d
f37122
f78f20
f68e4e

Requirements
Must have
• - Lic number 381526
• - phone number (805) 555-0148‬
• - quennbuilderscrew.com
• - Logo/Branding
Nice to have
• Quote from Gerard of Norvelle-
• HE WHO WORKS WITH HIS HANDS IS A LABORER.
• HE WHO WORKS WITH HIS HANDS & HIS HEAD IS A CRAFTSMAN.
• HE WHO WORKS WITH HIS HANDS & HIS HEAD & HIS HEART IS AN ARTISAN.
• -GERARD OF NORVELLE
• OR the below statement-
• Built with True Heart
Should not have
• Any additional verbiage not specified above including any type of verbiage about what kind of company we are. For instance- Integrity, reputable... It's just all played out. Im just looking for a bitching design that has the info that compliments my logo/branding.

```html
<!DOCTYPE html>
<html lang="en">
<head>
<meta charset="utf-8">
<title>Quenn Builders Crew – Yard Sign</title>
<link rel="stylesheet" href="https://fonts.googleapis.com/css2?family=Montserrat:wght@500;600;700;800&display=swap">
<style>
  :root {
    --canvas-bg: #e9e7e3;
    --sign-white: #ffffff;
    --brand-orange: #f37122;
    --brand-orange-light: #f78f20;
    --brand-brown: #8c7864;
    --ink: #111111;
  }
  * { box-sizing: border-box; margin: 0; padding: 0; }
  html, body {
    width: 1200px;
    height: 1000px;
    overflow: hidden;
    background: var(--canvas-bg);
    font-family: "Montserrat", Arial, sans-serif;
  }
  .canvas {
    position: relative;
    width: 1200px;
    height: 1000px;
  }
  .yard-sign {
    position: absolute;
    left: 280px;
    top: 90px;
    width: 630px;
    height: 820px;
    background: var(--sign-white);
    box-shadow: 0 6px 24px rgba(0,0,0,0.12);
    overflow: hidden;
  }
  .top-rule {
    position: absolute;
    left: 0;
    top: 14px;
    width: 100%;
    height: 5px;
    background: var(--brand-orange);
  }
  .brand-block {
    position: absolute;
    left: 0;
    top: 70px;
    width: 100%;
    display: flex;
    flex-direction: column;
    align-items: center;
  }
  .brand-square {
    width: 170px;
    height: 170px;
    background: var(--brand-brown);
  }
  .brand-name {
    margin-top: 36px;
    font-weight: 700;
    color: var(--brand-brown);
    text-align: center;
    line-height: 1;
  }
  .brand-name-main {
    display: block;
    font-size: 42px;
    letter-spacing: 4px;
  }
  .brand-name-sub {
    display: block;
    margin-top: 6px;
    font-size: 15px;
    letter-spacing: 1px;
  }
  .sale-band {
    position: absolute;
    left: 0;
    top: 368px;
    width: 100%;
    height: 128px;
    background: linear-gradient(180deg, var(--brand-orange) 0%, var(--brand-orange-light) 100%);
    display: flex;
    align-items: center;
    justify-content: center;
  }
  .sale-title {
    font-weight: 700;
    font-size: 86px;
    color: var(--sign-white);
    letter-spacing: 1px;
  }
  .contact-block {
    position: absolute;
    left: 0;
    top: 508px;
    width: 100%;
    text-align: center;
    color: var(--ink);
  }
  .phone {
    font-weight: 700;
    font-size: 54px;
    line-height: 1.1;
  }
  .website {
    margin-top: 6px;
    font-weight: 600;
    font-size: 28px;
  }
  .license {
    margin-top: 10px;
    font-weight: 500;
    font-size: 19px;
    letter-spacing: 0.5px;
  }
  .divider {
    position: absolute;
    left: 90px;
    top: 666px;
    width: 455px;
    height: 2px;
    background: var(--brand-orange);
  }
  .tagline {
    position: absolute;
    left: 0;
    top: 714px;
    width: 100%;
    text-align: center;
    font-weight: 600;
    font-size: 32px;
    color: var(--ink);
  }
  .bottom-tab {
    position: absolute;
    left: 268px;
    bottom: 10px;
    width: 102px;
    height: 40px;
    background: var(--brand-orange);
  }
</style>
</head>
<body>
  <main class="canvas">
    <section class="yard-sign">
      <div class="top-rule"></div>

      <div class="brand-block">
        <div class="brand-square"></div>
        <p class="brand-name">
          <span class="brand-name-main">QUENN</span>
          <span class="brand-name-sub">BUILDERS CREW INC.</span>
        </p>
      </div>

      <div class="sale-band">
        <h1 class="sale-title">FOR SALE</h1>
      </div>

      <div class="contact-block">
        <p class="phone">(805) 555-0148</p>
        <p class="website">www.quennbuilderscrew.com</p>
        <p class="license">LIC NUMBER 381526</p>
      </div>

      <div class="divider"></div>

      <p class="tagline">Built with True Heart</p>

      <div class="bottom-tab"></div>
    </section>
  </main>
</body>
</html>
```